Fizz's Shed & Grill Burger Restaurant Website - HomePage Only PSD

I need a website design for a restaurant called "Fizz's Shed and Grill" featuring burgers, wings, beer, live music, trivia, and more. I have several images of the restaurant and they already have their logo files created (see attached). I want some type of wood background and integrate the silver tin. This needs to be a modern, hip and fun type design. Design must incorporate these attached graphics.

UPDATE - just added a few more images of things I really like to be incorporated into my designs.
Updates

Industry/Entity Type

Burger Restaurant

Number of Pages Required

1 page

Font styles to use
Sans Serif

Requirements
Must have
• Restaurant/Bar theme with integration of existing logo and the red wood look.
Nice to have
• - Modern Fun appearance
• - Use Pelko Fonts

```html
<!DOCTYPE html>
<html lang="en">
<head>
<meta charset="utf-8">
<title>Fizz's Shed and Grill</title>
<link rel="stylesheet" href="https://fonts.googleapis.com/css2?family=Caveat+Brush&family=Open+Sans:wght@400;600;700&display=swap">
<style>
:root{
  --wood-dark:#2e1409;
  --wood-mid:#5a2a14;
  --wood-light:#7a3d1f;
  --cream:#f3e9df;
  --white:#ffffff;
  --red:#d41f1f;
  --rust:#a33a12;
  --maroon:#5e0f0f;
  --ink:#222222;
  --line:#d3d3d3;
  --star:#f2c200;
  --map:#e6e1d8;
}
*{box-sizing:border-box;margin:0;padding:0}
html,body{width:1200px;height:2765px;overflow:hidden}
body{position:relative;font-family:"Open Sans",Arial,sans-serif;color:var(--cream);
  background:linear-gradient(180deg,var(--wood-mid) 0%,var(--wood-light) 18%,var(--wood-mid) 35%,var(--wood-light) 55%,var(--wood-mid) 70%,var(--wood-dark) 100%)}
.abs{position:absolute}

/* header */
.brand{left:83px;top:40px;width:300px;height:100px;display:flex;align-items:center;gap:12px}
.brand-dot{width:52px;height:52px;border-radius:50%;border:3px solid var(--white);flex:none}
.brand-name{font-family:"Caveat Brush",cursive;font-size:30px;line-height:1.05;color:var(--white)}
.book-btn{left:805px;top:18px;width:155px;height:43px;border-radius:22px;background:#111;border:2px solid var(--white);color:var(--white);font-size:16px;font-weight:600;display:flex;align-items:center;gap:10px;padding-left:6px}
.book-btn .ico{width:30px;height:30px;border-radius:50%;background:var(--white)}
.social{display:flex;gap:10px}
.social span{width:26px;height:26px;border-radius:50%;background:var(--white);display:block}
.header-social{left:990px;top:26px}
.phone{left:972px;top:78px;font-size:18px;font-weight:600;color:var(--white);display:flex;align-items:center;gap:8px}
.nav{top:124px;left:440px;display:flex;align-items:center;font-size:15px;color:var(--white)}
.nav a{color:var(--white);text-decoration:none;padding:0 20px;border-left:1px solid rgba(255,255,255,.35)}
.nav a:first-child{border-left:none}

/* hero */
.hero{left:0;top:179px;width:1200px;height:488px}
.hero-panel{position:absolute;top:0;height:488px}
.hero-food{left:0;width:400px;background:radial-gradient(ellipse at 45% 50%,#d8a35a,#7a3a12 60%,#2a1206)}
.hero-drink{left:400px;width:402px;background:radial-gradient(ellipse at 50% 60%,#c9862f,#5a1010 55%,#1a0505)}
.hero-music{left:802px;width:398px;background:radial-gradient(ellipse at 40% 55%,#c7b48a,#2c3a5a 55%,#0b0e18)}
.tag{position:absolute;height:55px;display:flex;align-items:center;justify-content:center;font-family:"Caveat Brush",cursive;font-size:32px;color:var(--white)}
.tag-food{left:219px;top:11px;width:181px;background:var(--rust)}
.tag-drink{left:617px;top:85px;width:185px;background:var(--red)}
.tag-music{left:1017px;top:153px;width:183px;background:var(--maroon)}
.hero-band{position:absolute;left:0;top:414px;width:1200px;height:74px;background:rgba(30,15,10,.6);display:flex;align-items:center;justify-content:center;font-family:"Caveat Brush",cursive;font-size:46px;color:var(--white)}
.hero-arrow{position:absolute;top:200px}

/* welcome */
.welcome{left:81px;top:740px;width:705px}
.welcome h1{font-family:"Caveat Brush",cursive;font-weight:400;font-size:32px;color:var(--white);margin-bottom:10px}
.welcome p{font-size:13.3px;line-height:24px;color:var(--cream)}
.btn-outline{display:inline-block;border:1px solid var(--white);border-radius:4px;color:var(--white);font-size:13px;padding:6px 18px;text-transform:uppercase}
.read-more{left:81px;top:993px}

.booking{left:835px;top:746px;width:282px;height:316px;background:var(--white);border:4px solid #ece7e3}
.booking-tab{position:absolute;left:18px;top:0;width:234px;height:46px;background:#2b2b2b;color:var(--white);font-family:"Caveat Brush",cursive;font-size:26px;display:flex;align-items:center;justify-content:center}
.field{position:absolute;left:14px;width:249px;height:32px;border:1px solid var(--line);border-radius:3px;color:#555;font-size:12px;display:flex;align-items:center;justify-content:space-between;padding:0 10px}
.submit{position:absolute;left:14px;top:264px;width:120px;height:32px;background:#2b2b2b;color:var(--white);border-radius:4px;font-size:14px;font-weight:600;display:flex;align-items:center;justify-content:center}

/* features */
.features{left:0;top:1128px;width:1200px;height:356px;display:flex;border-top:2px solid #ddd;border-bottom:2px solid #ddd}
.feature{flex:1;position:relative;text-align:center;border-right:2px solid #ddd;padding:56px 22px 0}
.feature:last-child{border-right:none}
.feature h2{font-family:"Caveat Brush",cursive;font-weight:400;font-size:34px;color:var(--white);margin-bottom:8px}
.feature p{font-size:12.5px;line-height:20px;color:var(--white)}
.feature .plus{margin-top:12px;font-size:20px;color:var(--white)}
.f-burgers{background:linear-gradient(180deg,#5c3a1c,#3c2414 50%,#6a3c1a)}
.f-wings{background:linear-gradient(180deg,#4a2a18,#2e1a10 50%,#5a3420)}
.f-beer{background:linear-gradient(180deg,#6b4a22,#3a2410 50%,#8a5a1e)}
.f-music{background:linear-gradient(180deg,#3a1e14,#1e100a 50%,#4a2618)}
.f-trivia{background:linear-gradient(180deg,#5a1a14,#2a100a 50%,#3a2a18)}

/* testimonials */
.section-title{position:absolute;left:0;width:1200px;text-align:center;font-family:"Caveat Brush",cursive;font-weight:400;font-size:32px}
.testi-title{top:1518px;color:var(--white)}
.avatar{position:absolute;width:134px;height:134px;border-radius:50%;border:4px solid var(--white);background:radial-gradient(circle at 50% 40%,#c99b7c,#6d4a3a)}
.quote{position:absolute;width:330px;font-size:13.3px;line-height:21px;color:var(--cream)}
.quote .mark{font-family:Georgia,serif;font-size:48px;color:rgba(255,255,255,.35);position:absolute;line-height:1}
.stars{position:absolute;color:var(--star);font-size:16px;letter-spacing:1px}
.name{position:absolute;font-family:"Caveat Brush",cursive;font-size:14px;color:var(--cream)}
.dot-btn{position:absolute;top:1788px;width:26px;height:26px;border-radius:50%;display:flex;align-items:center;justify-content:center}

/* gallery */
.gallery{left:0;top:1865px;width:1200px;height:461px;background:var(--white);box-shadow:0 6px 10px rgba(0,0,0,.35)}
.gallery-title{top:50px;color:var(--ink)}
.g-circle{position:absolute;top:102px;width:240px;height:240px;border-radius:50%;border:2px solid #333;padding:10px;background:var(--white)}
.g-circle div{width:100%;height:100%;border-radius:50%}
.g-a{background:linear-gradient(180deg,#7fb3e0,#c7d7e6 55%,#b99a6a)}
.g-b{background:radial-gradient(circle at 50% 55%,#c9822f,#4a2a14 70%)}
.g-c{background:linear-gradient(180deg,#8fb8dc,#8a5a3a 50%,#4a3020)}
.g-d{background:radial-gradient(circle at 50% 50%,#b04a2a,#4a1a0c 75%)}
.view-all{position:absolute;left:536px;top:374px;width:124px;height:39px;border:1px solid #333;border-radius:4px;color:var(--ink);font-size:13px;display:flex;align-items:center;justify-content:center}

/* footer */
.footer{left:0;top:2326px;width:805px;height:439px}
.footer h3{position:absolute;left:103px;top:50px;font-family:"Caveat Brush",cursive;font-weight:400;font-size:30px;color:var(--white)}
.info{position:absolute;display:flex;gap:14px;font-size:14.5px;line-height:20px;color:var(--white)}
.info b{display:block;font-weight:700}
.map{position:absolute;left:520px;top:80px;width:190px;height:190px;background:var(--map);border:4px solid var(--white);border-radius:50% 50% 50% 0;transform:rotate(-45deg)}
.copyright{position:absolute;left:0;top:360px;width:805px;text-align:center;font-size:12.5px;color:var(--cream)}
.tin{left:805px;top:2326px;width:395px;height:439px;background:linear-gradient(90deg,#8c959c,#c3c9cd 20%,#8c959c 40%,#c3c9cd 60%,#8c959c 80%,#b5bcc1)}
.tin-mark{position:absolute;left:82px;top:104px;width:230px;height:230px;border-radius:50%;border:6px solid #2a2a2a;display:flex;align-items:center;justify-content:center;text-align:center}
.tin-mark span{font-family:"Caveat Brush",cursive;font-size:34px;line-height:1.1;color:#2a2a2a}
</style>
</head>
<body>

<header>
  <div class="abs brand"><span class="brand-dot"></span><span class="brand-name">Fizz's Shed and Grill</span></div>
  <div class="abs book-btn"><span class="ico"></span>Book A Table</div>
  <div class="abs social header-social"><span></span><span></span><span></span><span></span></div>
  <div class="abs phone">
    <svg width="20" height="20" viewBox="0 0 20 20"><circle cx="10" cy="10" r="9" fill="none" stroke="#fff" stroke-width="1.6"/><path d="M6.5 5.5l2 .2.8 2.2-1.2 1a6 6 0 0 0 3 3l1-1.2 2.2.8.2 2c-4.5.6-8.6-3.5-8-8z" fill="#fff"/></svg>
    (01) 555 0142
  </div>
  <nav class="abs nav">
    <a><svg width="26" height="22" viewBox="0 0 26 22"><path d="M13 2L2 12h3v9h6v-6h4v6h6v-9h3z" fill="#fff"/></svg></a>
    <a>About Us</a><a>Our Menus</a><a>Gallery</a><a>Reservations</a><a>Contact Us</a>
  </nav>
</header>

<section class="abs hero">
  <div class="hero-panel hero-food" role="img" aria-label="Photo of a crispy chicken burger with lettuce and tomato"></div>
  <div class="hero-panel hero-drink" role="img" aria-label="Photo of a martini and a whiskey cocktail"></div>
  <div class="hero-panel hero-music" role="img" aria-label="Photo of a hand playing an electric guitar"></div>
  <div class="tag tag-food">Food</div>
  <div class="tag tag-drink">Drink</div>
  <div class="tag tag-music">Music</div>
  <svg class="hero-arrow" style="left:20px" width="24" height="60" viewBox="0 0 24 60"><path d="M20 2L4 30l16 28" fill="none" stroke="#fff" stroke-width="2"/></svg>
  <svg class="hero-arrow" style="left:1156px" width="24" height="60" viewBox="0 0 24 60"><path d="M4 2l16 28L4 58" fill="none" stroke="#fff" stroke-width="2"/></svg>
  <div class="hero-band">Coming Soon To Cedar Hollow, Ms!</div>
</section>

<section class="abs welcome">
  <h1>Welcome to Fizz's Shed and Grill</h1>
  <p>Lorem ipsum dolor sit amet, consectetur adipiscing elit. Sed vitae magna tellus. Aenean ante nunc, semper nec cursus non, rutrum ac eros. Vestibulum mattis justo ac dui bibendum consequat a ac ipsum. Praesent a arcu venenatis, auctor velit eu, suscipit libero. Quisque convallis, leo ac pharetra sagittis, ipsum arcu auctor urna, sit amet cursus risus augue in eros. Duis lacinia nisi vitae leo commodo, non finibus magna maximus. Lorem ipsum dolor sit amet, consectetur adipiscing elit. Sed vitae magna tellus. Aenean ante nunc, semper nec cursus non, rutrum ac eros. Vestibulum mattis justo ac dui bibendum consequat a ac ipsum. Lorem ipsum dolor sit amet, consectetur adipiscing elit. Sed vitae magna tellus.</p>
</section>
<div class="abs btn-outline read-more">Read More</div>

<form class="abs booking">
  <div class="booking-tab">Book A Table</div>
  <div class="field" style="top:64px">Name</div>
  <div class="field" style="top:103px">Phone</div>
  <div class="field" style="top:142px">No. of Person
    <svg width="10" height="6" viewBox="0 0 10 6"><path d="M0 0h10L5 6z" fill="#555"/></svg></div>
  <div class="field" style="top:181px">Date
    <svg width="16" height="16" viewBox="0 0 16 16"><rect x="1" y="3" width="14" height="12" fill="none" stroke="#555"/><path d="M1 7h14M5 1v4M11 1v4" stroke="#555"/></svg></div>
  <div class="field" style="top:220px">Time
    <svg width="16" height="16" viewBox="0 0 16 16"><circle cx="8" cy="8" r="7" fill="none" stroke="#555"/><path d="M8 4v4h3" fill="none" stroke="#555"/></svg></div>
  <div class="submit">SUBMIT</div>
</form>

<section class="abs features">
  <article class="feature f-burgers" role="img" aria-label="Photo of a burger">
    <h2>Burgers</h2><p>Lorem ipsum dolor sit amet, consectetur adipiscing elit. Sed vitae magna tellus. Aenean ante nunc, semper nec cursus non. Lorem ipsum sit.</p><div class="plus">[+]</div>
  </article>
  <article class="feature f-wings" role="img" aria-label="Photo of grilled chicken wings">
    <h2>Wings</h2><p>Lorem ipsum dolor sit amet, consectetur adipiscing elit. Sed vitae magna tellus. Aenean ante nunc, semper nec cursus non. Lorem ipsum sit.</p><div class="plus">[+]</div>
  </article>
  <article class="feature f-beer" role="img" aria-label="Photo of a frothy glass of beer">
    <h2>Beer</h2><p>Lorem ipsum dolor sit amet, consectetur adipiscing elit. Sed vitae magna tellus. Aenean ante nunc, semper nec cursus non. Lorem ipsum sit.</p><div class="plus">[+]</div>
  </article>
  <article class="feature f-music" role="img" aria-label="Photo of a stage microphone">
    <h2>Live Music</h2><p>Lorem ipsum dolor sit amet, consectetur adipiscing elit. Sed vitae magna tellus. Aenean ante nunc, semper nec cursus non. Lorem ipsum sit.</p><div class="plus">[+]</div>
  </article>
  <article class="feature f-trivia" role="img" aria-label="Photo of a trivia night buzzer at the bar">
    <h2>Trivia</h2><p>Lorem ipsum dolor sit amet, consectetur adipiscing elit. Sed vitae magna tellus. Aenean ante nunc, semper nec cursus non. Lorem ipsum sit.</p><div class="plus">[+]</div>
  </article>
</section>

<section class="testimonials">
  <h2 class="section-title testi-title">Happy Customers</h2>

  <div class="avatar" style="left:83px;top:1576px" role="img" aria-label="Portrait of a smiling customer"></div>
  <div class="quote" style="left:243px;top:1600px"><span class="mark" style="left:-12px;top:-6px">&ldquo;</span>
    <p style="padding-left:27px">Duis autem vel eum iriure dolor in hendrerit in vulputate velitj esse molestie consequat, vel illum dolore eu feugiat nulla facilis sis at vero eros et accumsan et delenit facilisi.</p></div>
  <div class="stars" style="left:243px;top:1698px">&#9733;&#9733;&#9733;&#9733;</div>
  <div class="name" style="left:243px;top:1730px">Mr. Sam Kettering</div>

  <div class="avatar" style="left:638px;top:1576px" role="img" aria-label="Portrait of a customer holding a burger"></div>
  <div class="quote" style="left:798px;top:1600px"><span class="mark" style="left:-12px;top:-6px">&ldquo;</span>
    <p style="padding-left:27px">Duis autem vel eum iriure dolor in hendrerit in vulputate velitj esse molestie consequat, vel illum dolore eu feugiat nulla facilis sis at vero eros et accumsan et delenit facilisi.</p></div>
  <div class="stars" style="left:798px;top:1698px">&#9733;&#9733;&#9733;&#9733;</div>
  <div class="name" style="left:798px;top:1730px">Mr. Sam Kettering</div>

  <div class="dot-btn" style="left:578px;background:#fff"><svg width="10" height="12" viewBox="0 0 10 12"><path d="M8 1L2 6l6 5" fill="none" stroke="#222" stroke-width="2"/></svg></div>
  <div class="dot-btn" style="left:612px;background:#111"><svg width="10" height="12" viewBox="0 0 10 12"><path d="M2 1l6 5-6 5" fill="none" stroke="#fff" stroke-width="2"/></svg></div>
</section>

<section class="abs gallery">
  <h2 class="section-title gallery-title">Our Gallery</h2>
  <svg class="abs" style="left:30px;top:188px" width="20" height="74" viewBox="0 0 20 74"><path d="M18 2L2 37l16 35" fill="none" stroke="#333" stroke-width="2"/></svg>
  <div class="g-circle" style="left:83px"><div class="g-a" role="img" aria-label="Photo of a painted cow statue outside the restaurant"></div></div>
  <div class="g-circle" style="left:350px"><div class="g-b" role="img" aria-label="Photo of a cheeseburger"></div></div>
  <div class="g-circle" style="left:616px"><div class="g-c" role="img" aria-label="Photo of the wooden patio and stairs"></div></div>
  <div class="g-circle" style="left:881px"><div class="g-d" role="img" aria-label="Painting of a red cow"></div></div>
  <svg class="abs" style="left:1150px;top:188px" width="20" height="74" viewBox="0 0 20 74"><path d="M2 2l16 35L2 72" fill="none" stroke="#333" stroke-width="2"/></svg>
  <div class="view-all">VIEW ALL</div>
</section>

<footer class="abs footer">
  <h3>Contact Details</h3>
  <div class="info" style="left:103px;top:118px">
    <svg width="14" height="18" viewBox="0 0 14 18"><path d="M7 1a6 6 0 0 0-6 6c0 4.5 6 10 6 10s6-5.5 6-10a6 6 0 0 0-6-6z" fill="#fff"/><circle cx="7" cy="7" r="2.2" fill="#5a2a14"/></svg>
    <div><b>Address</b>18 Millpond Lane, Cedar Hollow, MS</div>
  </div>
  <div class="info" style="left:103px;top:180px">
    <svg width="16" height="16" viewBox="0 0 16 16"><circle cx="8" cy="8" r="7" fill="none" stroke="#fff" stroke-width="1.6"/><path d="M8 4v4h3" fill="none" stroke="#fff" stroke-width="1.6"/></svg>
    <div><b>Opening Hours</b>Mon - Sat 10-2300<br>Sun 11-2200</div>
  </div>
  <div class="info" style="left:325px;top:180px">
    <svg width="16" height="16" viewBox="0 0 16 16"><path d="M3 1l3 .3 1 3-1.6 1.4a8 8 0 0 0 4 4L11 8l3 1 .3 3C8.5 13 2.5 7 3 1z" fill="#fff"/></svg>
    <div><b>Reservation</b>(01) 555 0142</div>
  </div>
  <div class="info" style="left:103px;top:264px">
    <svg width="16" height="16" viewBox="0 0 16 16"><circle cx="12" cy="3" r="2.3" fill="#fff"/><circle cx="4" cy="8" r="2.3" fill="#fff"/><circle cx="12" cy="13" r="2.3" fill="#fff"/><path d="M12 3L4 8l8 5" fill="none" stroke="#fff" stroke-width="1.4"/></svg>
    <div><b>Follow Us</b></div>
  </div>
  <div class="abs social" style="left:148px;top:296px"><span style="width:34px;height:34px"></span><span style="width:34px;height:34px"></span><span style="width:34px;height:34px"></span><span style="width:34px;height:34px"></span></div>
  <div class="map" role="img" aria-label="Map showing the restaurant location"></div>
  <p class="copyright">Copyright &copy; 2016 Fizz's Shed and Grill. All Rights Reserved.</p>
</footer>

<aside class="abs tin" role="img" aria-label="Corrugated silver tin panel with the restaurant name">
  <div class="tin-mark"><span>Fizz's Shed<br>and Grill</span></div>
</aside>

</body>
</html>
```